Interior Stylist business card design needed

I need a business card for my new company in Sydney called "Liv Harrowby Designs". The business offers an interior styling and colour consultancy. My clients are generally not very design savvy (hence why they use me) and can range from being quite conservative to really wanting something "out there". They can be looking for a budget makeover or something more expensive / substantial. I'd like my business card design to be stylish (but not overly formal). I certainly don't want it to be conservative. I'd like it to stand out a bit! I don't really have any aversion to particular colours and I don't have a logo as such - my business name is really all I have.

Target Market(s)

As above - home owners, ranging from conservative to modern

Industry/Entity Type

Conservative

Contact Information for Business Card

Liv Harrowby Designs
Colour consultancy and interior styling
ph: 0417 238 605
email: livharrowby@qoralnet.net.au

Requirements
Should not have
• Old fashioned writing or motifs. No Times Roman font!!

```html
<!DOCTYPE html>
<html lang="en">
<head>
<meta charset="utf-8">
<title>Liv Harrowby Designs – Business Cards</title>
<link rel="stylesheet" href="https://fonts.googleapis.com/css2?family=Cinzel:wght@400;500&family=Open+Sans:wght@400&display=swap">
<style>
  :root {
    --backdrop: #e9e7e2;
    --card-charcoal: #3e403e;
    --accent-lime: #d5d400;
    --text-soft: #d9d9d3;
    --card-w: 520px;
    --card-h: 300px;
  }
  * { box-sizing: border-box; margin: 0; padding: 0; }
  html, body {
    width: 1200px; height: 787px; overflow: hidden;
    background: var(--backdrop);
  }
  .stage {
    width: 1200px; height: 787px;
    display: flex; align-items: center; justify-content: center; gap: 56px;
  }
  .card {
    position: relative;
    width: var(--card-w); height: var(--card-h);
    background: var(--card-charcoal);
    overflow: hidden;
    box-shadow: 0 6px 18px rgba(0,0,0,0.18);
  }
  .card svg.card-art { position: absolute; inset: 0; width: 100%; height: 100%; }

  /* Contact side */
  .brand-block {
    position: absolute; top: 62px; left: 0; right: 0;
    text-align: center;
  }
  .brand-name {
    font-family: "Cinzel", serif; font-weight: 400;
    font-size: 25px; letter-spacing: 1px;
    color: var(--accent-lime);
  }
  .brand-tagline {
    font-family: "Open Sans", sans-serif; font-size: 12px;
    letter-spacing: 9px; color: var(--text-soft);
    margin-top: 4px; padding-left: 9px;
  }
  .contact-list {
    position: absolute; left: 22px; top: 190px;
    list-style: none;
    font-family: "Open Sans", sans-serif; font-size: 10.5px;
    color: var(--card-charcoal);
  }
  .contact-list li { display: flex; align-items: center; gap: 7px; height: 17px; white-space: nowrap; }
  .contact-icon {
    width: 11px; height: 11px; border-radius: 2px;
    background: var(--card-charcoal);
    display: inline-flex; align-items: center; justify-content: center;
    flex: none;
  }
  .contact-icon svg { width: 8px; height: 8px; }
  .name-mark {
    position: absolute; right: 34px; top: 236px;
    font-family: "Cinzel", serif; font-size: 17px;
    color: var(--card-charcoal);
    white-space: nowrap;
  }

  /* Front side */
  .front-name-mark {
    position: absolute; left: 108px; top: 96px;
    font-family: "Cinzel", serif; font-size: 30px;
    color: var(--accent-lime);
    white-space: nowrap;
  }
  .front-name {
    position: absolute; left: 150px; top: 146px;
    font-family: "Cinzel", serif; font-size: 21px; letter-spacing: 1px;
    color: var(--accent-lime);
    white-space: nowrap;
  }
  .front-web {
    position: absolute; left: 132px; top: 214px;
    font-family: "Open Sans", sans-serif; font-size: 10px;
    color: var(--accent-lime);
  }
</style>
</head>
<body>
<main class="stage">

  <!-- Contact side -->
  <section class="card card--contact" aria-label="Business card, contact side">
    <svg class="card-art" viewBox="0 0 520 300" aria-hidden="true">
      <polygon points="0,150 520,222 520,272 0,272" fill="var(--accent-lime)"/>
      <line x1="0" y1="162" x2="230" y2="196" stroke="var(--card-charcoal)" stroke-width="1.5"/>
    </svg>
    <div class="brand-block">
      <div class="brand-name">LIV HARROWBY</div>
      <div class="brand-tagline">DESIGNS</div>
    </div>
    <ul class="contact-list">
      <li>
        <span class="contact-icon"><svg viewBox="0 0 10 10"><path d="M2 1 L4 1 L4.6 3 L3.5 3.8 Q4.5 5.8 6.2 6.5 L7 5.4 L9 6 L9 8 Q5 9 1.5 5 Q1 3 2 1Z" fill="var(--accent-lime)"/></svg></span>
        0417 238 605
      </li>
      <li>
        <span class="contact-icon"><svg viewBox="0 0 10 10"><rect x="1" y="2.5" width="8" height="5.5" fill="none" stroke="var(--accent-lime)" stroke-width="1"/><path d="M1 2.5 L5 5.5 L9 2.5" fill="none" stroke="var(--accent-lime)" stroke-width="1"/></svg></span>
        livharrowby@qoralnet.net.au
      </li>
      <li>
        <span class="contact-icon"></span>
        www.socialpage.net/livharrowby
      </li>
    </ul>
    <div class="name-mark">Liv Harrowby</div>
  </section>

  <!-- Front side -->
  <section class="card card--front" aria-label="Business card, front side">
    <svg class="card-art" viewBox="0 0 520 300" aria-hidden="true">
      <polyline points="22,128 22,22 300,22" fill="none" stroke="var(--accent-lime)" stroke-width="7"/>
      <polyline points="300,278 498,278 498,150" fill="none" stroke="var(--accent-lime)" stroke-width="9"/>
      <line x1="330" y1="30" x2="498" y2="30" stroke="var(--accent-lime)" stroke-width="2"/>
      <line x1="22" y1="270" x2="250" y2="270" stroke="var(--accent-lime)" stroke-width="2"/>
    </svg>
    <div class="front-name-mark">Liv Harrowby</div>
    <div class="front-name">LIV HARROWBY</div>
    <div class="front-web">www.livharrowby.com</div>
  </section>

</main>
</body>
</html>
```